Kelo Wave Mint Business cards

Logo, tag line and photo on card
Agent Name
Title
Address
Phone number
Email
Website
Make logo on one side large by rotating  to portrait format.  Keep the background of the logo white.

Contact Information for Business Card
Slogan; Making Every Wave Count

```html
<!DOCTYPE html>
<html lang="en">
<head>
<meta charset="UTF-8">
<title>Kelo Wave Mint – Business Cards</title>
<link rel="stylesheet" href="https://fonts.googleapis.com/css2?family=Montserrat:wght@500;600;800&display=swap">
<style>
  :root {
    --backdrop: #a4a5a7;
    --card: #ffffff;
    --navy: #2c3a78;
    --red: #cc2230;
    --photo-light: #d9d9d9;
    --photo-dark: #4a4a4c;
  }
  * { box-sizing: border-box; margin: 0; padding: 0; }
  html, body {
    width: 1200px; height: 781px; overflow: hidden;
    background: var(--backdrop);
    font-family: "Montserrat", sans-serif;
  }
  .sheet {
    width: 1200px; height: 781px;
    display: flex; justify-content: center; align-items: center; gap: 110px;
  }
  .card {
    width: 354px; height: 620px;
    background: var(--card);
    border-radius: 22px;
    display: flex; flex-direction: column; align-items: center;
  }
  /* Front */
  .card--front { padding-top: 46px; }
  .agent-name {
    color: var(--red); font-weight: 800; font-size: 24px; letter-spacing: 1px;
  }
  .agent-title {
    color: var(--navy); font-weight: 600; font-size: 16px; letter-spacing: 1px; margin-top: 2px;
  }
  .portrait-frame {
    margin-top: 22px;
    width: 270px; height: 300px;
    border: 5px solid var(--red);
    border-radius: 28px;
    padding: 4px;
  }
  .portrait {
    width: 100%; height: 100%;
    border-radius: 22px;
    background: linear-gradient(160deg, var(--photo-light) 0%, #a9a9ab 45%, var(--photo-dark) 100%);
  }
  .address {
    margin-top: 22px; text-align: center;
    color: var(--navy); font-weight: 500; font-size: 15px; line-height: 1.4;
  }
  .contact-icons { display: flex; gap: 10px; margin-top: 12px; }
  .contact-icons svg { width: 16px; height: 16px; }
  .contact-list {
    list-style: none; text-align: center; margin-top: 10px;
    color: var(--navy); font-weight: 500; font-size: 15px; line-height: 1.45;
  }
  .contact-list .phone { letter-spacing: 3px; }
  /* Back */
  .card--back { justify-content: center; position: relative; }
  .brand-name {
    color: var(--navy); font-weight: 800; font-size: 54px; line-height: 1.02;
    text-align: center; letter-spacing: -1px;
  }
  .tagline {
    position: absolute; bottom: 52px;
    color: var(--navy); font-weight: 600; font-size: 16px; letter-spacing: 0.5px;
  }
</style>
</head>
<body>
<main class="sheet">
  <section class="card card--front">
    <h1 class="agent-name">MARCUS HALE</h1>
    <p class="agent-title">Founder</p>
    <div class="portrait-frame">
      <div class="portrait" role="img" aria-label="Portrait photo of the founder, smiling, in a patterned dark shirt on a white background"></div>
    </div>
    <p class="address">Suite 210, 85 - 9th Street<br>NE, Redwater, AB, T0A 2W0</p>
    <div class="contact-icons" aria-hidden="true">
      <svg viewBox="0 0 16 16"><circle cx="8" cy="8" r="8" fill="var(--red)"/><path d="M5.2 4.2l1.4 1.5-.8 1.1c.5 1 1.3 1.8 2.3 2.3l1.1-.8 1.5 1.4-.9 1.3c-2.9-.4-5.1-2.6-5.5-5.5z" fill="#fff"/></svg>
      <svg viewBox="0 0 16 16"><rect x="1" y="3" width="14" height="10" rx="1.5" fill="var(--red)"/><path d="M1.5 4l6.5 5 6.5-5" fill="none" stroke="#fff" stroke-width="1.3"/></svg>
      <svg viewBox="0 0 16 16"><circle cx="8" cy="8" r="8" fill="var(--red)"/><g fill="none" stroke="#fff" stroke-width="1"><circle cx="8" cy="8" r="5"/><ellipse cx="8" cy="8" rx="2.2" ry="5"/><path d="M3 8h10"/></g></svg>
    </div>
    <ul class="contact-list">
      <li class="phone">403 555 0142</li>
      <li>contact@kelowavemint.com</li>
      <li>www.kelowavemint.com</li>
    </ul>
  </section>

  <section class="card card--back">
    <p class="brand-name">Kelo<br>Wave<br>Mint</p>
    <p class="tagline">Making Every Wave Count</p>
  </section>
</main>
</body>
</html>
```